Letter design, envelope design, and more

Hello, we the Tavrin Gmbh are looking for our shop. Letter C5. Design does not have to be like a business card, so it can have straight lines. Only the color is important. The logo is the text under TaVRin omit.It should not be playful but Profesionel

Font styles to use
Sans Serif

Colors
0555a3
3176b5
85abd2
85cae6
34a7d8
0792cd
cee9f5
cfdfed
000000

Requirements
Must have
• Color like business card, Please, with the text under TaVRin, Correct address Lindmattstr. 4 Zip code 9517 Goldach, as well as Couvert Without addressing only design and logo with TaVrn
Nice to have
• more writing articles
Should not have
• Not too colored, Text under TaVRin, bright colors

```html
<!DOCTYPE html>
<html lang="de">
<head>
<meta charset="utf-8">
<title>Tavrin Gmbh – Geschäftsausstattung</title>
<link href="https://fonts.googleapis.com/css2?family=Lato:wght@400;700&family=Kaushan+Script&display=swap" rel="stylesheet">
<style>
  :root{
    --navy:#2b2d6b;
    --slate:#7d95ab;
    --stage:#cbcccf;
    --paper:#ffffff;
    --ink:#3a3a40;
    --rule:#b9bcc2;
  }
  *{box-sizing:border-box;margin:0;padding:0}
  html,body{width:1200px;height:630px;overflow:hidden}
  body{background:var(--stage);font-family:"Lato",sans-serif;color:var(--ink);position:relative}

  .brand{display:flex;align-items:center;gap:6px;color:var(--navy);font-weight:700;letter-spacing:1px}
  .brand-square{background:var(--navy);flex:none}

  /* Letterhead */
  .letterhead{position:absolute;left:38px;top:42px;width:388px;height:546px;
    background:linear-gradient(160deg,#ffffff 35%,#e9eaec 100%);box-shadow:0 0 0 1px #c3c5c9}
  .letterhead .brand{position:absolute;left:24px;top:18px;font-size:22px}
  .letterhead .brand-square{width:26px;height:26px}
  .contact{position:absolute;left:297px;top:10px;border-left:1px solid var(--rule);padding-left:6px;
    font-size:7.2px;line-height:9px;color:var(--ink)}
  .contact li{list-style:none;display:flex;gap:3px;margin-bottom:3px}
  .contact svg{width:7px;height:7px;flex:none;margin-top:1px}
  .greeting{position:absolute;left:22px;top:96px;font-size:10px;font-weight:700;color:var(--navy)}
  .body-copy{position:absolute;left:22px;top:111px;width:348px;font-size:6.9px;line-height:11.6px;text-align:justify;color:var(--ink)}
  .body-copy p{margin-bottom:8.5px}
  .closing{position:absolute;left:22px;top:424px;font-size:11.5px}
  .signature{position:absolute;left:22px;top:442px;font-family:"Kaushan Script",cursive;font-size:17px;color:var(--navy)}

  .footer-band{position:absolute;left:0;right:0;bottom:0;height:18px}
  .footer-band svg{position:absolute;inset:0;width:100%;height:100%}
  .footer-band .web{position:absolute;right:18px;bottom:3px;color:#fff;font-size:9.5px;letter-spacing:1.4px}

  /* Envelopes */
  .envelope{position:absolute;width:576px;height:258px;background:var(--paper);box-shadow:0 0 0 1px #b5b8bd}
  .envelope .flap{position:absolute;left:0;top:0;width:576px;height:104px}
  .envelope-back{left:585px;top:60px}
  .envelope-back .brand{position:absolute;left:0;right:0;top:38px;justify-content:center;color:#fff;font-size:24px}
  .envelope-middle{left:543px;top:170px}
  .envelope-middle .brand{position:absolute;left:0;right:0;top:40px;justify-content:center;font-size:24px}
  .envelope-front{left:447px;top:286px;height:257px}
  .envelope-front .brand{position:absolute;left:22px;top:16px;font-size:24px}
  .envelope-front .brand-square{width:28px;height:28px}
  .envelope-front .address{position:absolute;left:23px;top:66px;font-size:10.5px;display:flex;gap:4px;align-items:center}
  .envelope-front .address svg{width:9px;height:9px}
  .envelope-front .footer-band .web{right:28px}
</style>
</head>
<body>

<article class="letterhead">
  <div class="brand"><span class="brand-square"></span>TAVRIN</div>
  <ul class="contact">
    <li><svg viewBox="0 0 10 10"><circle cx="5" cy="5" r="4.3" fill="none" stroke="#2b2d6b"/><circle cx="5" cy="4.3" r="1.4" fill="#2b2d6b"/></svg><span>Lindmattstr. 4<br>9517 Goldach</span></li>
    <li><svg viewBox="0 0 10 10"><circle cx="5" cy="5" r="4.3" fill="none" stroke="#2b2d6b"/><path d="M3.5 3c0 2 1.5 3.5 3.5 3.8" stroke="#2b2d6b" fill="none" stroke-width="1.2"/></svg><span>+41 71 555 02 48</span></li>
    <li><svg viewBox="0 0 10 10"><rect x="1" y="2.5" width="8" height="5.5" fill="#2b2d6b"/><path d="M1 2.5l4 3 4-3" stroke="#fff" fill="none" stroke-width=".8"/></svg><span>info@tavrin.ch</span></li>
  </ul>

  <p class="greeting">Dear Mr. Lorem,</p>
  <div class="body-copy">
    <p>Lorem ipsum dolor sit amet, consectetuer adipiscing elit, sed diam nonummy nibh euismod tincidunt ut laoreet dolore magna aliquam erat volutpat. Ut wisi enim ad minim veniam, quis nostrud exerci tation ullamcorper suscipit lobortis nisl ut aliquip ex ea commodo consequat. Duis autem vel eum iriure dolor in hendiusto odio dignissim qui blandit praesent luptatum zzril delenit.facilisi.</p>
    <p>Lorem ipsum dolor sit amet, consectetuer adipiscing elit, sed diam nonummy nibh euismod tincidunt ut laoreet dolore magna aliquam erat volutpat. Ut wisi enim ad minim veniam, quis nostrud exerci tation ullamcorper suscipit lobortis nisl ut aliquip ex ea commodo consequat.</p>
    <p>Lorem ipsum dolor sit amet, consectetuer adipiscing elit, sed diam nonummy nibh euismod tincidunt ut laoreet dolore magna aliquam erat volutpat. Ut wisi enim ad minim veniam, quis nostrud exerci tation ullamcorper suscipit lobortis nisl ut aliquip ex ea commodo consequat. Duis autem vel eum iriure dolor in hendiusto odio dignissim qui blandit praesent luptatum zzril delenit.facilisi.</p>
    <p>Lorem ipsum dolor sit amet, consectetuer adipiscing elit, sed diam nonummy nibh euismod tincidunt ut laoreet dolore magna aliquam erat volutpat. Ut wisi enim ad minim veniam, quis nostrud exerci tation ullamcorper suscipit lobortis nisl ut aliquip ex ea commodo consequat.</p>
    <p>Lorem ipsum dolor sit amet, consectetuer adipiscing elit, sed diam nonummy nibh euismod tincidunt ut laoreet dolore magna aliquam erat volutpat. Ut wisi enim ad minim veniam, quis nostrud exerci tation ullamcorper suscipit lobortis nisl ut aliquip ex ea commodo consequat. Duis autem vel eum iriure dolor in hendiusto odio dignissim qui blandit praesent luptatum zzril delenit.facilisi.</p>
    <p>Lorem ipsum dolor sit amet, consectetuer adipiscing elit, sed diam nonummy nibh euismod tincidunt ut laoreet dolore magna aliquam erat volutpat. Ut wisi enim ad minim veniam, quis nostrud exerci tation ullamcorper suscipit lobortis nisl ut aliquip ex ea commodo consequat.</p>
  </div>
  <p class="closing">Sincerely Your,</p>
  <p class="signature">Your Name</p>

  <div class="footer-band">
    <svg viewBox="0 0 388 18" preserveAspectRatio="none">
      <rect x="0" y="10" width="250" height="8" fill="#7d95ab"/>
      <polygon points="256,18 274,0 388,0 388,18" fill="#2b2d6b"/>
    </svg>
    <span class="web">www.tavrin.ch</span>
  </div>
</article>

<section class="envelope envelope-back">
  <svg class="flap" viewBox="0 0 576 104">
    <path d="M0 0H576C571 32 566 42 540 50L310 100Q288 104 266 100L36 50C10 42 5 32 0 0Z" fill="#7d95ab"/>
  </svg>
  <div class="brand">TAVRIN</div>
</section>

<section class="envelope envelope-middle">
  <svg class="flap" viewBox="0 0 576 104">
    <path d="M0 0C5 30 10 38 40 45L270 98Q288 102 306 98L536 45C566 38 571 30 576 0" fill="none" stroke="#b5b8bd"/>
  </svg>
  <div class="brand">TAVRIN</div>
</section>

<section class="envelope envelope-front">
  <div class="brand"><span class="brand-square"></span>TAVRIN</div>
  <p class="address">
    <svg viewBox="0 0 10 10"><circle cx="5" cy="5" r="4.3" fill="none" stroke="#3a3a40"/><circle cx="5" cy="4.3" r="1.4" fill="#3a3a40"/></svg>
    Lindmattstr. 4, 9517 Goldach
  </p>
  <div class="footer-band">
    <svg viewBox="0 0 576 18" preserveAspectRatio="none">
      <rect x="0" y="10" width="424" height="8" fill="#7d95ab"/>
      <polygon points="429,18 446,0 576,0 576,18" fill="#2b2d6b"/>
    </svg>
    <span class="web">www.tavrin.ch</span>
  </div>
</section>

</body>
</html>
```